Pet Sitting Business Card

Would like a business card designed for my new pet sitting business
Card needs to match with logo design.
Blue and Orange are the theme colours.

Simple yet sophisticated design

company name:- MEADOWLARK PET CARE
Dana Kovich
Owner
0452716093
dana@meadowlarkpetcare.com.au
www.meadowlarkpetcare.com.au

I'm going to close my deadline early. I will be picking a winner by the 10th of May. Please submit designs before then.
thank you

Target Market(s)

All types of professional pet lovers wishing to have their pet looked after

Industry/Entity Type

Pet

Requirements
Must have
• Logo design
Blue and orange

```html
<!DOCTYPE html>
<html lang="en">
<head>
<meta charset="utf-8">
<title>Meadowlark Pet Care – Business Card</title>
<link rel="stylesheet" href="https://fonts.googleapis.com/css2?family=Exo+2:wght@400;500;600&display=swap">
<style>
  :root {
    --stage: #e9ecef;
    --card: #ffffff;
    --blue-deep: #1e88ee;
    --blue-light: #4fb6e2;
    --orange: #e8892a;
    --ink: #2b2b2b;
    --name-blue: #2b92e4;
  }
  * { box-sizing: border-box; margin: 0; padding: 0; }
  html, body {
    width: 1200px; height: 894px; overflow: hidden;
    background: var(--stage);
    font-family: "Exo 2", sans-serif;
  }
  .business-card {
    position: absolute; left: 100px; top: 161px;
    width: 1000px; height: 572px;
    background: var(--card);
    box-shadow: 0 10px 30px rgba(0,0,0,.18);
    overflow: hidden;
  }
  .card-swoosh { position: absolute; inset: 0; width: 100%; height: 100%; }
  .brand {
    position: absolute; left: 600px; top: 140px; width: 340px;
    display: flex; align-items: center; gap: 16px;
  }
  .brand-dot {
    flex: none; width: 44px; height: 44px; border-radius: 50%;
    background: var(--orange);
  }
  .brand-name {
    color: var(--blue-deep); font-weight: 600; font-size: 34px;
    line-height: 1.05; letter-spacing: 2px;
  }
  .person {
    position: absolute; right: 70px; top: 335px; text-align: left;
  }
  .person-name {
    color: var(--name-blue); font-size: 30px; font-weight: 500; letter-spacing: 3px;
  }
  .person-role {
    color: var(--ink); font-size: 22px; font-weight: 500; letter-spacing: 1.5px; margin-top: 2px;
  }
  .contact-list {
    position: absolute; left: 34px; top: 372px; list-style: none;
  }
  .contact-item {
    display: flex; align-items: center; gap: 12px;
    color: #fff; font-size: 19px; height: 36px; letter-spacing: .5px;
  }
  .contact-icon { width: 22px; height: 22px; flex: none; }
</style>
</head>
<body>
  <div class="business-card">
    <svg class="card-swoosh" viewBox="0 0 1000 572" preserveAspectRatio="none" aria-hidden="true">
      <defs>
        <linearGradient id="blueSweep" x1="0" y1="0" x2="1" y2="0">
          <stop offset="0" stop-color="#1e88ee"/>
          <stop offset="0.55" stop-color="#4fb6e2"/>
          <stop offset="1" stop-color="#1e88ee"/>
        </linearGradient>
      </defs>
      <path d="M0,170 Q420,520 1000,470 L1000,572 L0,572 Z" fill="url(#blueSweep)"/>
      <path d="M0,80 Q420,440 960,455 Q420,455 0,125 Z" fill="#e8892a"/>
    </svg>

    <div class="brand">
      <span class="brand-dot"></span>
      <span class="brand-name">MEADOWLARK<br>PET CARE</span>
    </div>

    <div class="person">
      <div class="person-name">DANA KOVICH</div>
      <div class="person-role">OWNER</div>
    </div>

    <ul class="contact-list">
      <li class="contact-item">
        <svg class="contact-icon" viewBox="0 0 22 22"><circle cx="11" cy="11" r="11" fill="#fff"/><path d="M7 6l3 0 1 3-2 1c1 2 2 3 4 4l1-2 3 1 0 3c-6 0-10-4-10-10z" fill="#1e88ee"/></svg>
        <span>0452716093</span>
      </li>
      <li class="contact-item">
        <svg class="contact-icon" viewBox="0 0 22 22"><circle cx="11" cy="11" r="11" fill="#fff"/><rect x="7.5" y="4.5" width="7" height="13" rx="1.5" fill="#1e88ee"/><rect x="9" y="6.5" width="4" height="8" fill="#fff"/></svg>
        <span>0452716093</span>
      </li>
      <li class="contact-item">
        <svg class="contact-icon" viewBox="0 0 22 22"><circle cx="11" cy="11" r="11" fill="#fff"/><rect x="5" y="7" width="12" height="8" rx="1" fill="#1e88ee"/><path d="M5.5 7.5l5.5 4 5.5-4" stroke="#fff" stroke-width="1.2" fill="none"/></svg>
        <span>dana@meadowlarkpetcare.com.au</span>
      </li>
      <li class="contact-item">
        <svg class="contact-icon" viewBox="0 0 22 22"><circle cx="11" cy="11" r="11" fill="#fff"/><g fill="none" stroke="#1e88ee" stroke-width="1.3"><circle cx="11" cy="11" r="6"/><ellipse cx="11" cy="11" rx="2.6" ry="6"/><path d="M5 11h12"/></g></svg>
        <span>www.meadowlarkpetcare.com.au</span>
      </li>
      <li class="contact-item">
        <svg class="contact-icon" viewBox="0 0 22 22"><circle cx="11" cy="11" r="11" fill="#fff"/><path d="M11 4a4.5 4.5 0 0 0-4.5 4.5c0 3.5 4.5 9 4.5 9s4.5-5.5 4.5-9A4.5 4.5 0 0 0 11 4z" fill="#1e88ee"/><circle cx="11" cy="8.6" r="1.7" fill="#fff"/></svg>
        <span>14 Wattle Lane, Brookfield QLD</span>
      </li>
    </ul>
  </div>
</body>
</html>
```